Create modern and sleek business card for luxury real estate company

We're a "boutique" real estate office looking for a design that gets across a highly modern luxury brand. Blacks and whites are probably the best colors unless we try a silver foil for the logo. I've attached a version of our current logo here. I'd like to swap out the current font on there with Gotham Light Regular.

I'm looking to have one side of the card have the logo with the space for our agents info on the other side.

Target Market(s)

Young professionals in a "luxury" headspace

Industry/Entity Type

Real estate

Contact Information for Business Card

A place for agent name, cell number, website. The slogan "Simply Rethinking Real Estate".

Font styles to use
Other font styles liked:
• Gotham Regular

Colors

Designer to choose only greyscale colors for use in the design.

Requirements
Must have
• Matte black as the background color. Clean lines and use of contrast. A specific design aspect that will use silver foil.
Nice to have
• Up in the air on integrating a QR code
Should not have
• Any houses or other real estate related design (ex: a clip art house)

```html
<!DOCTYPE html>
<html lang="en">
<head>
<meta charset="utf-8">
<title>Halden Estates – Business Card</title>
<link href="https://fonts.googleapis.com/css2?family=Tinos:wght@400;700&family=Lato:wght@400&display=swap" rel="stylesheet">
<style>
  :root {
    --backdrop: #151515;
    --card-white: #ffffff;
    --card-dark: #333333;
    --ink: #2b2b2b;
    --paper-text: #ffffff;
    --silver: #a3a3a3;
  }
  * { margin: 0; padding: 0; box-sizing: border-box; }
  html, body { width: 1075px; height: 1200px; overflow: hidden; background: var(--backdrop); }
  .canvas { position: relative; width: 1075px; height: 1200px; }
  .card { position: absolute; left: 206px; width: 663px; height: 395px; overflow: hidden; }
  .card--front { top: 187px; background: var(--card-white); }
  .card--back { top: 637px; background: var(--card-dark); }

  .card__artwork {
    position: absolute; left: 0; right: 0; top: 175px; bottom: 0;
    background: linear-gradient(to bottom, rgba(51,51,51,0) 0%, var(--card-dark) 28%, var(--card-dark) 100%);
  }

  .brand { position: absolute; }
  .brand__circle { position: absolute; border-radius: 50%; }
  .brand__name { position: absolute; font-family: "Tinos", serif; font-weight: 400; white-space: nowrap; line-height: 1; }

  .card--front .brand__circle { left: 36px; top: 79px; width: 80px; height: 80px; border: 2px solid var(--ink); }
  .card--front .brand__name { left: 131px; color: var(--ink); font-size: 38px; }
  .card--front .brand__name--top { top: 84px; }
  .card--front .brand__name--bottom { top: 124px; left: 142px; }

  .agent { position: absolute; right: 37px; top: 52px; text-align: right; color: var(--ink); }
  .agent__name { font-family: "Tinos", serif; font-weight: 700; font-size: 25px; line-height: 1; letter-spacing: 0.5px; }
  .agent__title { font-family: "Lato", sans-serif; font-size: 18px; line-height: 1; margin-top: 4px; margin-right: 5px; }

  .contact { position: absolute; right: 38px; color: var(--paper-text); font-family: "Lato", sans-serif; font-size: 18px; line-height: 1; text-align: right; }
  .contact__line { position: absolute; right: 0; white-space: nowrap; display: flex; align-items: center; gap: 8px; }
  .contact__icon { width: 18px; height: 18px; flex: none; }
  .contact--list { top: 245px; }
  .contact--list .contact__line:nth-child(1) { top: 0; }
  .contact--list .contact__line:nth-child(2) { top: 25px; }
  .contact--list .contact__line:nth-child(3) { top: 50px; }
  .address { position: absolute; right: 38px; top: 334px; color: var(--paper-text); font-family: "Lato", sans-serif; font-size: 18px; line-height: 23px; display: flex; gap: 8px; align-items: flex-start; }
  .address__text { text-align: left; }

  .card--back .brand__circle { left: 131px; top: 141px; width: 112px; height: 112px; border: 3px solid var(--silver); }
  .card--back .brand__name { color: var(--silver); font-size: 52px; }
  .card--back .brand__name--top { left: 264px; top: 150px; }
  .card--back .brand__name--bottom { left: 280px; top: 208px; }
</style>
</head>
<body>
<main class="canvas">
  <section class="card card--front" aria-label="Business card front">
    <div class="card__artwork" role="img" aria-label="Decorative flowing wave artwork in charcoal and white"></div>

    <div class="brand">
      <span class="brand__circle"></span>
      <span class="brand__name brand__name--top">HALDEN</span>
      <span class="brand__name brand__name--bottom">ESTATES</span>
    </div>

    <div class="agent">
      <p class="agent__name">MARCUS ELLERY</p>
      <p class="agent__title">Managing Director</p>
    </div>

    <div class="contact contact--list">
      <p class="contact__line">021-555 018 342
        <svg class="contact__icon" viewBox="0 0 24 24" aria-hidden="true"><path fill="#fff" d="M6.6 10.8a15 15 0 0 0 6.6 6.6l2.2-2.2a1 1 0 0 1 1-.25 11.4 11.4 0 0 0 3.6.57 1 1 0 0 1 1 1V20a1 1 0 0 1-1 1A17 17 0 0 1 3 4a1 1 0 0 1 1-1h3.5a1 1 0 0 1 1 1c0 1.25.2 2.45.57 3.57a1 1 0 0 1-.25 1z"/></svg>
      </p>
      <p class="contact__line">hello@haldenestates.com
        <svg class="contact__icon" viewBox="0 0 24 24" aria-hidden="true"><path fill="#fff" d="M2 5h20v14H2z"/><path fill="none" stroke="#333" stroke-width="1.6" d="M2.5 5.5 12 13l9.5-7.5"/></svg>
      </p>
      <p class="contact__line">www.haldenestates.com
        <svg class="contact__icon" viewBox="0 0 24 24" aria-hidden="true"><circle cx="12" cy="12" r="10" fill="#fff"/><g fill="none" stroke="#333" stroke-width="1.3"><ellipse cx="12" cy="12" rx="4" ry="10"/><path d="M2 12h20M4 7h16M4 17h16"/></g></svg>
      </p>
    </div>

    <div class="address">
      <p class="address__text">87, Linden Court Row<br>Westvale, 30418</p>
      <svg class="contact__icon" viewBox="0 0 24 24" aria-hidden="true"><path fill="#fff" d="M12 2a7 7 0 0 0-7 7c0 5 7 13 7 13s7-8 7-13a7 7 0 0 0-7-7zm0 9.5A2.5 2.5 0 1 1 12 6.5a2.5 2.5 0 0 1 0 5z"/></svg>
    </div>
  </section>

  <section class="card card--back" aria-label="Business card back">
    <div class="brand">
      <span class="brand__circle"></span>
      <span class="brand__name brand__name--top">HALDEN</span>
      <span class="brand__name brand__name--bottom">ESTATES</span>
    </div>
  </section>
</main>
</body>
</html>
```